Interior designer needs a power point template design

I need a template PowerPoint design for my client presentations. The presentations I prepare for my clients usually include the furniture project, the detail of the selected furniture, and the costs. There are a lot of images I insert. What I need is to have a template that I can use for all my presentations, where from time to time I will insert the specific images and descriptions I want to insert. What will always be the same will be the cover, the colors, the font, and the design of the internal sections.
I already have my logo that I would like to insert on each page of the presentation (in small size).
In summary, I need:
- basic template design
- cover with an image chosen by Pictavale photo
- design an internal section/chapter
- internal page design.

I like the clolors of pink and brown <8please see image attached)
Images (will come from Pictavale photo)
● entrance/hall
● living room
● dining room
● Bathroom
● Closet
● Kids room
● Master bedroom
● Master bathroom
● Kitchen
● Office
● Laundry
● Balcony or Terrace

Target Market(s)

Customers (both residential and commercial projects)

Industry/Entity Type

interior design

Font styles to use
Other font styles liked:
• I like courier new

Requirements
Must have
• beautiful design
Should not have
• animations

```html
<!DOCTYPE html>
<html lang="en">
<head>
<meta charset="utf-8">
<title>Casa Ventura – Presentation Template</title>
<link rel="stylesheet" href="https://fonts.googleapis.com/css2?family=Oswald:wght@300;400;500;700&family=Roboto:wght@400&display=swap">
<style>
:root{
  --page:#101010;
  --terracotta:#bb7a66;
  --ink:#1c1c1c;
  --charcoal:#464646;
  --paper:#ffffff;
  --rule:#b0705e;
  --body:#333333;
}
*{margin:0;padding:0;box-sizing:border-box}
html,body{width:1200px;height:3861px;overflow:hidden;background:var(--page)}
body{position:relative;font-family:'Roboto',sans-serif;color:var(--body)}
.slide{position:absolute;left:64px;width:1070px;height:601px;background:var(--paper);overflow:hidden}
.abs{position:absolute}
.heading{font-family:'Oswald',sans-serif;font-weight:400;color:var(--ink);letter-spacing:.5px}
.brand-name{position:absolute;font-family:'Oswald',sans-serif;font-weight:400;color:var(--charcoal);white-space:nowrap;line-height:1}
.line{position:absolute;background:var(--rule)}

/* cover */
.cover{top:67px;background:var(--terracotta)}
.cover-photo{position:absolute;inset:0;background:linear-gradient(180deg,#c48470 0%,#bd7b66 55%,#b77562 100%)}
.cover-welcome{position:absolute;left:0;width:1070px;top:180px;text-align:center;font-family:'Oswald',sans-serif;font-size:56px;color:#fff;font-weight:400}
.cover-name{position:absolute;left:0;width:1070px;top:300px;text-align:center;font-family:'Oswald',sans-serif;font-size:56px;line-height:68px;color:var(--ink);font-weight:400}

/* feature page */
.feature{top:689px}
.feature-title{left:45px;top:50px;font-size:38px;font-weight:300}
.feature-text{left:45px;top:112px;width:390px;font-size:15px;line-height:22.4px;text-align:justify;color:var(--body)}
.feature-photo{left:482px;top:0;width:588px;height:601px;background:linear-gradient(180deg,#6d6a5e 0%,#4f5663 55%,#2b3440 72%,#9a6a3c 100%)}

/* rooms overview */
.rooms{top:1314px}
.room{position:absolute;top:58px;width:314px}
.room-photo{width:314px;height:310px}
.room-title{margin-top:32px;text-align:center;font-family:'Oswald',sans-serif;font-size:34px;font-weight:400;color:var(--ink)}
.room-text{margin:18px auto 0;width:300px;text-align:center;font-size:11.5px;line-height:19.5px;color:var(--body)}

/* chapter */
.chapter{top:1945px}
.chapter-band{left:0;top:50px;width:121px;height:492px;background:var(--terracotta)}
.chapter-label{position:absolute;left:60px;top:246px;transform:translate(-50%,-50%) rotate(-90deg);white-space:nowrap;font-family:'Oswald',sans-serif;font-size:40px;font-weight:400;color:var(--ink)}
.chapter-photo{left:121px;top:50px;width:499px;height:492px;background:linear-gradient(160deg,#f6e6c8 0%,#f1d9b4 50%,#7fa7d6 70%,#c7a571 100%)}
.chapter-headbox{left:643px;top:70px;width:376px;height:90px;border-left:2px solid var(--ink);border-right:2px solid var(--ink)}
.chapter-head{left:662px;top:73px;font-family:'Oswald',sans-serif;font-weight:500;font-size:28px;line-height:37px;color:var(--ink)}
.chapter-lead{left:661px;top:180px;width:358px;font-size:11.5px;line-height:22px;color:var(--body)}
.chapter-col{top:293px;width:165px;font-size:11.5px;line-height:22px;text-align:justify;color:var(--body)}

/* bathroom */
.bath{top:2571px;background:var(--terracotta)}
.bath-photo{left:0;top:0;width:1070px;height:314px;background:linear-gradient(180deg,#8d8d8d 0%,#b9b9b9 60%,#d9d9d9 100%)}
.bath-title{left:295px;top:342px;font-family:'Oswald',sans-serif;font-weight:300;font-size:42px;color:#fff}
.bath-text{left:297px;top:404px;width:705px;font-size:12px;line-height:19.6px;color:#f7e8e2}

/* closing */
.closing{top:3205px;background:var(--charcoal)}
.closing-photo-top{left:0;top:0;width:1070px;height:129px;background:linear-gradient(90deg,#f0f0f0,#e4e1de 50%,#f0f0f0)}
.closing-photo-bottom{left:0;top:469px;width:1070px;height:132px;background:linear-gradient(90deg,#ececec,#dcd8d4 50%,#ececec)}
.closing-band{left:0;top:129px;width:1070px;height:340px;background:var(--charcoal)}
.closing-col{left:743px;width:232px;background:var(--terracotta)}
.thanks{left:743px;top:278px;width:232px;text-align:center;font-family:'Oswald',sans-serif;font-weight:700;font-size:50px;color:#fff;line-height:60px;background:var(--charcoal)}
.contact{position:absolute;left:353px;display:flex;align-items:center;gap:16px}
.contact-icon{width:56px;height:56px;border-radius:50%;background:var(--terracotta);display:flex;align-items:center;justify-content:center;flex:none}
.contact-label{font-family:'Oswald',sans-serif;font-weight:500;font-size:15px;color:#fff;line-height:24px}
.contact-value{font-family:'Oswald',sans-serif;font-weight:300;font-size:15px;color:#fff;line-height:24px}
</style>
</head>
<body>

<!-- Cover -->
<section class="slide cover">
  <div class="cover-photo" role="img" aria-label="Faded living room with sofa, shelves of books and floor lamp"></div>
  <div class="cover-welcome">WELCOME TO</div>
  <div class="cover-name">CASA VENTURA</div>
</section>

<!-- Feature page -->
<section class="slide feature">
  <div class="line" style="left:22px;top:30px;width:2px;height:76px"></div>
  <div class="line" style="left:22px;top:34px;width:136px;height:2px"></div>
  <h2 class="abs heading feature-title">MASTER BEDROOM</h2>
  <p class="abs feature-text">Sed ut perspiciatis unde omnis iste natus error sit voluptatem accusantium doloremque laudantium, totam rem aperiam, eaque ipsa quae ab illo inventore veritatis et quasi architecto beatae vitae dicta sunt explicabo. Nemo enim ipsam voluptatem quia voluptas sit aspernatur aut odit aut fugit, sed quia consequuntur magni dolores eos qui ratione voluptatem sequi nesciunt. Neque porro quisquam est, qui dolorem ipsum quia dolor sit amet, consectetur, adipisci velit, sed quia non numquam eius modi tempora incidunt ut labore et dolore magnam aliquam quaerat voluptatem. sed quia non numquam .quasi architecto beatae vitae dicta sunt explicabo. Nemo enim ipsam voluptatem quia voluptas sit aspernatur aut odit aut fugit, sed quia consequuntur magni dolores eos qui ratione voluptatem sequi nesciunt. quasi architecto beatae vitae dicta sunt explicabo. Nemo enim ipsam voluptatem.</p>
  <div class="line" style="left:456px;top:440px;width:2px;height:120px"></div>
  <div class="line" style="left:322px;top:555px;width:136px;height:2px"></div>
  <div class="abs feature-photo" role="img" aria-label="Master bedroom render with patterned wallpaper, chandelier, dark bed and wooden floor"></div>
  <div class="brand-name" style="right:12px;bottom:16px;font-size:14px">Casa Ventura</div>
</section>

<!-- Rooms overview -->
<section class="slide rooms">
  <article class="room" style="left:43px">
    <div class="room-photo" role="img" aria-label="Entrance hall illustration with armchairs, rug and pendant lamp" style="background:linear-gradient(180deg,#4d5a52 0%,#7f8a86 55%,#b4b6b8 100%)"></div>
    <h3 class="room-title">01.ENTRANCE/HALL</h3>
    <p class="room-text">Lorem ipsum dolor sit amet, consectetur adipiscing elit, sed do eiusmod tempor incididunt ut labore et dolore magna aliqua. Ut enim ad minim veniam, quis nostrud exercitation ullamco laboris nisi ut aliquip ex ea commodo consequat.</p>
  </article>
  <article class="room" style="left:383px">
    <div class="room-photo" role="img" aria-label="Living room illustration with yellow sofa, plants and floor lamp" style="background:linear-gradient(180deg,#f2d7a8 0%,#efc98b 60%,#d8703f 80%,#c9623a 100%)"></div>
    <h3 class="room-title">02.LIVING ROOM</h3>
    <p class="room-text">Lorem ipsum dolor sit amet, consectetur adipiscing elit, sed do eiusmod tempor incididunt ut labore et dolore magna aliqua. Ut enim ad minim veniam, quis nostrud exercitation ullamco laboris nisi ut aliquip ex ea commodo consequat.</p>
  </article>
  <article class="room" style="left:713px">
    <div class="room-photo" role="img" aria-label="Dining room illustration with wooden table, chairs and window" style="background:linear-gradient(180deg,#efdcb3 0%,#e8cf9d 55%,#7a4a2c 75%,#c79358 100%)"></div>
    <h3 class="room-title">03.DINING ROOM</h3>
    <p class="room-text">Lorem ipsum dolor sit amet, consectetur adipiscing elit, sed do eiusmod tempor incididunt ut labore et dolore magna aliqua. Ut enim ad minim veniam, quis nostrud exercitation ullamco laboris nisi ut aliquip ex ea commodo consequat.</p>
  </article>
  <div class="brand-name" style="right:12px;bottom:14px;font-size:13px">Casa Ventura</div>
</section>

<!-- Chapter -->
<section class="slide chapter">
  <div class="abs chapter-band"><span class="chapter-label">CAMERA PADRONALE</span></div>
  <div class="abs chapter-photo" role="img" aria-label="Bedroom illustration with bed, blue blanket, plants and window"></div>
  <div class="abs chapter-headbox"></div>
  <h2 class="abs chapter-head">LOREM IPSUM DOLOR SIT AMET<br>CONSECTETUR ADIPISCING ELIT.</h2>
  <p class="abs chapter-lead">Lorem ipsum dolor sit amet, consectetur adipiscing elit, sed do eiusmod tempor incididunt ut labore et dolore magna aliqua. Ut en im ad minim veniam, quis nostrud exercitation ullamco laboris nisi ut aliquip ex ea commodo consequat.</p>
  <p class="abs chapter-col" style="left:664px">Lorem ipsum dolor sit amet, consectetur adipiscing elit, sed do eiusmod tempor incididunt ut labore et dolore magna aliqua. Ut enim ad minim veniam, quis nostrud exercitation ullamco laboris nisi ut aliquip ex ea commodo consequat.</p>
  <p class="abs chapter-col" style="left:857px">Lorem ipsum dolor sit amet, consectetur adipiscing elit, sed do eiusmod tempor incididunt ut labore et dolore magna aliqua. Ut enim ad minim veniam, quis nostrud exercitation ullamco laboris nisi ut aliquip ex ea commodo consequat.</p>
  <div class="brand-name" style="right:12px;bottom:14px;font-size:13px">Casa Ventura</div>
</section>

<!-- Bathroom -->
<section class="slide bath">
  <div class="abs bath-photo" role="img" aria-label="Bathroom render with vessel sink on wooden stand, bidet and freestanding bathtub"></div>
  <div class="brand-name" style="left:50px;top:500px;font-size:32px">Casa Ventura</div>
  <div class="line" style="left:283px;top:330px;width:2px;height:70px;background:var(--ink)"></div>
  <h2 class="abs bath-title">Bathroom</h2>
  <p class="abs bath-text">Lorem ipsum dolor sit amet, consectetur adipiscing elit, sed do eiusmod tempor incididunt ut labore et dolore magna aliqua. Ut enim ad minim veniam, quis nostrud exercitation ullamco laboris nisi ut aliquip ex ea commodo consequat. Duis aute irure dolor in reprehenderit in voluptate velit esse cillum dolore eu fugiat nulla pariatur. Lorem ipsum dolor sit amet, consectetur adipiscing elit, sed do eiusmod tempor incididunt ut labore et dolore magna aliqua. Ut enim ad minim veniam, quis nostrud exercitation ullamco laboris nisi ut aliquip ex ea commodo consequat. Duis aute irure dolor in reprehenderit in voluptate velit esse cillum dolore eu fugiat nulla pariatur. Lorem ipsum dolor sit amet, consectetur adipiscing elit, sed do eiusmod tempor incididunt ut labore et dolore magna aliqua. Ut enim ad minim veniam, quis nostrud exercitation ullamco.</p>
  <div class="line" style="left:1017px;top:449px;width:2px;height:106px;background:var(--ink)"></div>
  <div class="line" style="left:937px;top:553px;width:82px;height:2px;background:var(--ink)"></div>
</section>

<!-- Closing -->
<section class="slide closing">
  <div class="abs closing-photo-top" role="img" aria-label="Faded walk-in closet with hanging clothes"></div>
  <div class="abs closing-band"></div>
  <div class="abs closing-photo-bottom" role="img" aria-label="Faded walk-in closet with hanging clothes"></div>
  <div class="abs closing-col" style="top:0;height:280px"></div>
  <div class="abs closing-col" style="top:340px;height:261px"></div>
  <div class="abs thanks">THANK YOU</div>

  <div class="brand-name" style="left:60px;top:280px;font-size:38px;color:#e8e8e8">Casa Ventura</div>

  <div class="contact" style="top:168px">
    <div class="contact-icon"><svg width="22" height="26" viewBox="0 0 22 26"><path d="M11 1C5.5 1 2 5 2 9.8 2 16 11 25 11 25s9-9 9-15.2C20 5 16.5 1 11 1z" fill="#fff"/><circle cx="11" cy="10" r="3.4" fill="#bb7a66"/></svg></div>
    <div><div class="contact-label">Location</div><div class="contact-value">Di Marta Lodovici&nbsp; via dei<br>Tigli, 42</div></div>
  </div>
  <div class="contact" style="top:280px">
    <div class="contact-icon"><svg width="24" height="24" viewBox="0 0 24 24"><path d="M6.6 10.8c1.4 2.8 3.8 5.1 6.6 6.6l2.2-2.2c.3-.3.7-.4 1-.2 1.1.4 2.3.6 3.6.6.6 0 1 .4 1 1V20c0 .6-.4 1-1 1C10.6 21 3 13.4 3 4c0-.6.4-1 1-1h3.5c.6 0 1 .4 1 1 0 1.3.2 2.5.6 3.6.1.3 0 .7-.2 1L6.6 10.8z" fill="#fff"/></svg></div>
    <div><div class="contact-label">Phone</div><div class="contact-value">+1 333/5550147</div></div>
  </div>
  <div class="contact" style="top:370px">
    <div class="contact-icon"><svg width="24" height="18" viewBox="0 0 24 18"><rect x="1.5" y="1.5" width="21" height="15" rx="1.5" fill="none" stroke="#fff" stroke-width="2"/><path d="M2 2.5l10 8 10-8" fill="none" stroke="#fff" stroke-width="2"/></svg></div>
    <div><div class="contact-label">Email</div><div class="contact-value">marta.lodovici@mailbox.it</div></div>
  </div>
</section>

</body>
</html>
```